Larkspur Talent IT Recruiting firm needs a business card design for Recruiters, Sourcers, and Account

We need business cards that allow us to change all contact info, names, titles (Recruiter, Sourcer, Account Manager, Director, CEO, etc) per person since we have three offices, in three cities, Phoenix, Austin, and Las Vegas. We do recruiting and contractors for IT positions (Developers, Architects, Software Engineers, Security Engineers, Help Desk, DBAs, PMs, Scrum Masters, etc.) Our client companies are very diverse from Meridian 100 to silicone Valley type start-ups.

So, while we what hip, techie, and quirky, it still needs to be professional. Primary color we use is blue, with silver as a secondary color.

Target Market(s)

IT, Technology

Industry/Entity Type

Business

Contact Information for Business Card

Company name: Larkspur Talent, Inc.
Website: www.larkspurtalent.example
Logos for Careerloop, Blipster, and Myriada

Name, Title, Office Number, Cell Number, email

Font styles to use
Serif
Sans Serif

Colors
0455a3
d5d5d5

Requirements
Nice to have
• The grey I selected below is not necessary - but, would like silver included. I included a card design (File 3: LTI early trial example.jpg) that I had started on. It's very rough, and not quite what we're looking for, but what we did like is the logo, big, maybe a bit faded, off center, goes out of frame, etc. Still looking for other ideas - you are the pros! But, just an idea of a design element we liked.

```html
<!DOCTYPE html>
<html lang="en">
<head>
<meta charset="utf-8">
<title>Larkspur Talent – Business Card</title>
<link href="https://fonts.googleapis.com/css2?family=Open+Sans:wght@400;700&display=swap" rel="stylesheet">
<style>
  :root{
    --accent-blue:#1e8fd8;
    --ink:#1c1c1c;
    --silver:#d5d5d5;
    --paper:#ffffff;
    --backdrop:#3a3a3a;
  }
  *{margin:0;padding:0;box-sizing:border-box}
  html,body{width:1200px;height:852px;overflow:hidden}
  body{
    background:var(--backdrop);
    font-family:"Open Sans",Arial,sans-serif;
    color:var(--ink);
    position:relative;
  }
  .card{
    position:absolute;
    top:289px;
    width:490px;height:280px;
    background:var(--paper);
    border-radius:12px;
    overflow:hidden;
  }
  .card--front{left:85px}
  .card--back{left:625px}

  .wordmark{
    position:absolute;
    font-family:"Open Sans",Arial,sans-serif;font-weight:700;
    color:var(--ink);letter-spacing:1px;white-space:nowrap;
  }
  .card--front .wordmark{left:0;right:0;top:118px;text-align:center;font-size:32px}
  .card--back .wordmark{right:28px;top:40px;font-size:20px}

  .rule{position:absolute;height:1px;background:var(--silver)}
  .rule--top{left:215px;right:28px;top:96px}
  .rule--name{left:60px;width:230px;top:177px}

  .person{position:absolute;left:22px;top:146px}
  .person__name{font-weight:700;color:var(--accent-blue);font-size:14px;letter-spacing:.3px}
  .person__title{font-size:11px;margin-top:4px}

  .contact-list{position:absolute;left:22px;top:200px;list-style:none;font-size:11.5px;line-height:16px}
  .contact-list li{display:flex;align-items:center;gap:9px}
  .contact-list svg{width:10px;height:10px;fill:var(--accent-blue);flex:none}

  .office{position:absolute;right:28px;top:112px;text-align:right;font-size:10.5px;line-height:15px}
  .social{display:flex;justify-content:flex-end;gap:6px;margin-bottom:6px}
  .social span{
    background:var(--accent-blue);color:var(--paper);font-size:8.5px;font-weight:700;
    padding:1px 5px;border-radius:2px;
  }
</style>
</head>
<body>

<section class="card card--front" aria-label="Card front">
  <div class="wordmark">LARKSPUR TALENT</div>
</section>

<section class="card card--back" aria-label="Card back">
  <div class="wordmark">LARKSPUR TALENT</div>
  <div class="rule rule--top"></div>

  <div class="office">
    <div class="social"><span>Blipster</span><span>Careerloop</span><span>Myriada</span></div>
    <div>4210 E Canyon Rd, Suite 210</div>
    <div>Phoenix, AZ 85044, USA</div>
  </div>

  <div class="person">
    <div class="person__name">DANA WHITCOMB</div>
    <div class="person__title">CEO</div>
  </div>
  <div class="rule rule--name"></div>

  <ul class="contact-list">
    <li><svg viewBox="0 0 10 10"><path d="M1 2c0-1 1-1.5 2-1.5l1 2-1 1c.6 1.3 1.4 2.1 2.7 2.7l1-1 2 1C8.7 7.7 8 9 7 9 3.5 9 1 5.5 1 2z"/></svg>602| 555-0142</li>
    <li><svg viewBox="0 0 10 10"><rect x="2.5" y="0.5" width="5" height="3"/><rect x="0.5" y="4" width="9" height="4" rx="1"/><rect x="2.5" y="7" width="5" height="2.5"/></svg>602| 555-0187</li>
    <li><svg viewBox="0 0 10 10"><path d="M0.5 2h9v6h-9z M0.5 2l4.5 3.5L9.5 2" stroke="#fff" stroke-width=".8"/></svg>dana@larkspurtalent.example</li>
    <li><svg viewBox="0 0 10 10"><circle cx="5" cy="5" r="4.5"/></svg>www.larkspurtalent.example</li>
  </ul>
</section>

</body>
</html>
```